Website Design Request - Management Consulting Firm

We need a Website designed for an IT Management Staffing and Recruiting firm called TRAVENOK based in San Francisco.

The firm is an high-end technology staffing agency. Our focus is on quality and high-caliber candidates rather than quantity.

The website will have two main home pages. One for the recruiter and another on for the candidates.

The website needs to optimize for mobile devices as well.

I have attached few mock-ups that I have done just to show what I am thinking. The UI needs to be very clean, fluid, and it needs to have a modern, rustic, professional feel to it.

Target Market(s)

Technology Manager, Director, VP, CIO of Companies that have $4b-10b dollar revenue. Such as larkspurdwellings.example , https://www.velmorian.example/, quillnet.example, zib.example

Industry/Entity Type

Management Consulting

Number of Pages Required

5+ page

Font styles to use
Sans Serif

Colors
f37122
ffffff

Requirements
Must have
• Please review mock-ups for suggestions
Nice to have
Should not have

```html
<!DOCTYPE html>
<html lang="en">
<head>
<meta charset="utf-8">
<title>TRAVENOK – IT Project Management Jobs</title>
<link href="https://fonts.googleapis.com/css2?family=Montserrat:wght@300;400;500&display=swap" rel="stylesheet">
<style>
  :root{
    --brand:#f37122;
    --accent:#ff9800;
    --ink:#333333;
    --muted:#9a9a9a;
    --line:#e6e6e6;
    --footer-bg:#fafafa;
    --dark-btn:#2b2b2b;
    --white:#ffffff;
  }
  *{box-sizing:border-box;margin:0;padding:0}
  html,body{width:879px;height:1200px;overflow:hidden;background:var(--white)}
  body{font-family:'Montserrat',sans-serif;color:var(--ink);position:relative}
  .abs{position:absolute}

  /* header */
  .site-header{position:absolute;left:0;top:0;width:879px;height:80px;background:var(--white)}
  .brand-name{position:absolute;left:148px;top:28px;font-size:23px;font-weight:500;letter-spacing:1px;color:var(--brand);line-height:1}
  .main-nav a{position:absolute;top:36px;font-size:11px;color:#555;text-decoration:none;font-weight:400}
  .btn-small{position:absolute;top:33px;height:21px;font-size:7px;line-height:21px;text-align:center;color:var(--white);text-decoration:none;letter-spacing:.3px}
  .btn-signin{left:614px;width:55px;background:var(--accent)}
  .btn-signup{left:677px;width:54px;background:var(--dark-btn)}

  /* hero */
  .hero{position:absolute;left:0;top:80px;width:879px;height:413px;
    background:radial-gradient(ellipse at 52% 40%, #6f7378 0%, #4c5156 45%, #35393d 100%)}
  .hero-title{position:absolute;left:0;width:879px;top:190px;text-align:center;font-size:23.5px;font-weight:400;color:var(--accent)}
  .hero-sub{position:absolute;left:0;width:879px;top:229px;text-align:center;font-size:12.5px;color:var(--white)}
  .email-field{position:absolute;left:197px;top:278px;width:485px;height:37px;background:var(--white);font-size:9px;color:#999;padding-left:14px;line-height:37px}
  .btn-offers{position:absolute;left:370px;top:334px;width:139px;height:28px;background:var(--accent);color:var(--white);font-size:8.5px;text-align:center;line-height:28px}
  .employer-link{position:absolute;left:0;width:879px;top:398px;text-align:center;font-size:9px;color:#eee}
  .employer-link span{color:var(--accent);text-decoration:underline}
  .slider-dots{position:absolute;left:421px;top:456px;display:flex;gap:5px}
  .slider-dots i{width:5px;height:5px;border-radius:50%;background:var(--white);display:block}
  .slider-dots i.on{background:var(--accent)}

  /* tabs */
  .tab-band{position:absolute;left:0;top:493px;width:879px;height:67px;background:var(--accent)}
  .tab{position:absolute;top:24px;font-size:15px;color:var(--white);font-weight:400}
  .tab-underline{position:absolute;left:246px;top:50px;width:92px;height:2px;background:var(--white)}

  /* steps */
  .steps-title{position:absolute;left:0;width:879px;top:615px;text-align:center;font-size:16px;color:var(--accent)}
  .steps-sub{position:absolute;left:0;width:879px;top:643px;text-align:center;font-size:7px;color:#aaa}
  .step-num{position:absolute;width:26px;height:26px;border-radius:50%;border:1px solid var(--line);text-align:center;line-height:25px;font-size:13px;color:#aaa;font-weight:300}
  .step-icon{position:absolute}
  .step-title{position:absolute;left:404px;font-size:9.5px;color:var(--ink)}
  .step-desc{position:absolute;left:405px;font-size:6.8px;color:#999;line-height:16.5px}
  .btn-upload{position:absolute;left:331px;top:918px;width:227px;height:40px;background:var(--accent);border-radius:2px;color:var(--white);font-size:13px;line-height:40px;padding-left:43px;letter-spacing:.3px}
  .btn-upload svg{position:absolute;left:20px;top:13px}

  /* footer */
  .site-footer{position:absolute;left:0;top:1006px;width:879px;height:159px;background:var(--footer-bg);border-top:1px solid #eee;border-bottom:1px solid #eee}
  .footer-brand{position:absolute;left:148px;top:29px;font-size:23px;font-weight:500;letter-spacing:1px;color:var(--brand);line-height:1}
  .footer-col{position:absolute;top:34px}
  .footer-col h4{font-size:9px;font-weight:400;color:var(--accent);margin-bottom:14px}
  .footer-col a{display:block;font-size:7px;color:#777;text-decoration:none;height:16.5px}
  .copyright{position:absolute;left:0;width:879px;top:1180px;text-align:center;font-size:7px;color:#555}
</style>
</head>
<body>

<header class="site-header">
  <div class="brand-name">TRAVENOK</div>
  <nav class="main-nav">
    <a href="#" style="left:463px">Professional</a>
    <a href="#" style="left:546px">Employers</a>
  </nav>
  <a href="#" class="btn-small btn-signin">&#10140; SIGN IN</a>
  <a href="#" class="btn-small btn-signup">&#10150; SIGN UP</a>
</header>

<section class="hero" role="img" aria-label="Photo of a smiling young professional in a striped shirt sitting at a desk in an office">
  <h1 class="hero-title">Looking for IT Project Management Jobs ?</h1>
  <p class="hero-sub">Upload your name resume,accept interview requests,get offers</p>
  <div class="email-field">Your E-mail Address</div>
  <div class="btn-offers">GET OFFERS NOW !</div>
  <p class="employer-link">Looking For Talents&nbsp; ?&nbsp; <span>See How It Works For Employers</span></p>
  <div class="slider-dots"><i class="on"></i><i></i><i></i><i></i></div>
</section>

<nav class="tab-band">
  <div class="tab" style="left:239px">How It Works ?</div>
  <div class="tab-underline"></div>
  <div class="tab" style="left:467px">Why Us ?</div>
</nav>

<section class="steps">
  <h2 class="steps-title">3 -Simple Steps</h2>
  <p class="steps-sub">Employers pay 25% more for a better FIT Project Manager</p>

  <div class="step-num" style="left:313px;top:704px">1</div>
  <svg class="step-icon" style="left:358px;top:700px" width="30" height="34" viewBox="0 0 30 34" fill="none" stroke="#ff9800" stroke-width="1.3">
    <path d="M2 1h18l8 8v24H2z"/><path d="M20 1v8h8"/><path d="M15 27V14M10 19l5-5 5 5"/>
  </svg>
  <div class="step-title" style="top:702px">Upload Your Resume</div>
  <div class="step-desc" style="top:717px">Answer few questions and upload your resume</div>

  <div class="step-num" style="left:313px;top:770px">2</div>
  <svg class="step-icon" style="left:356px;top:772px" width="33" height="24" viewBox="0 0 33 24" fill="none" stroke="#ff9800" stroke-width="1.3">
    <rect x="1" y="1" width="31" height="22"/><path d="M1 1l15.5 13L32 1M1 23l11-10M32 23L21 13"/>
  </svg>
  <div class="step-title" style="top:766px">We Send You Interview Request.</div>
  <div class="step-desc" style="top:781px">Interested in someone ? With a single click, send<br>interview request and let us handle the rest</div>

  <div class="step-num" style="left:313px;top:848px">3</div>
  <svg class="step-icon" style="left:354px;top:849px" width="38" height="24" viewBox="0 0 38 24" fill="none" stroke="#ff9800" stroke-width="1.3">
    <rect x="1" y="1" width="36" height="22"/><path d="M1 6a5 5 0 0 0 5-5M32 1a5 5 0 0 0 5 5M1 18a5 5 0 0 1 5 5M37 18a5 5 0 0 0-5 5"/>
    <text x="19" y="17" text-anchor="middle" font-family="Montserrat,sans-serif" font-size="13" fill="#ff9800" stroke="none">$</text>
  </svg>
  <div class="step-title" style="top:846px">Get $1000 Bonus</div>
  <div class="step-desc" style="top:861px">Find a job get $1000 bonus TRAVENOK</div>

  <div class="btn-upload">
    <svg width="12" height="15" viewBox="0 0 12 15" fill="none" stroke="#5a3a00" stroke-width="1.2"><path d="M6 15V1M1 6l5-5 5 5"/></svg>
    UPLOAD&nbsp; YOUR RESUME
  </div>
</section>

<footer class="site-footer">
  <div class="footer-brand">TRAVENOK</div>
  <div class="footer-col" style="left:339px"><h4>Job Seekers</h4><a href="#">How It Works</a><a href="#">Browse Jobs</a><a href="#">Create Profile</a></div>
  <div class="footer-col" style="left:466px"><h4>Clients</h4><a href="#">How It Works</a><a href="#">Browse Resumes</a><a href="#">Post Jobs for Free</a><a href="#">Sign Up</a></div>
  <div class="footer-col" style="left:587px"><h4>Services</h4><a href="#">Staffing</a><a href="#">Direct Hire</a></div>
  <div class="footer-col" style="left:686px"><h4>About Us</h4><a href="#">Our Mission</a><a href="#">Our Vision</a><a href="#">Our Values</a></div>
</footer>
<p class="copyright">© 2016 Company Name&nbsp; |&nbsp; All Rights Reserved</p>

</body>
</html>
```